New business card/stationary for a consulting company

I am looking for a clean and very professional looking business card for my consulting company as well as corresponding stationary. I am uploading our logo. I like simple and powerful for the feel. No graphics but I am open on everything else. Below is my contact information but would like the final to be in a version I can add my employees information into and print. Thank you.

Daniel Whitcombe
dan@ferncliffadvisory.com
2870 North 9th Avenue, Summit Floor, Elm Ridge, Illinois 60531
www.ferncliffadvisory.com

Industry/Entity Type

Consulting

Contact Information for Business Card

Daniel Whitcombe
dan@ferncliffadvisory.com
www.ferncliffadvisory.com

Font styles to use
Serif
Sans Serif

Requirements
Must have
• Our logo and the business card details.
Nice to have
• our website www.ferncliffadvisory.com

```html
<!DOCTYPE html>
<html lang="en">
<head>
<meta charset="utf-8">
<title>Ferncliff Advisory – Business Card</title>
<link href="https://fonts.googleapis.com/css2?family=Open+Sans:wght@400;700&family=Raleway:wght@300;400&display=swap" rel="stylesheet">
<style>
  :root {
    --backdrop: #3a332f;
    --card: #141414;
    --card-edge: #0b0b0b;
    --ink: #f2f2f2;
    --ink-soft: #9a9a9a;
    --mark: #bdbdbd;
  }
  * { margin: 0; padding: 0; box-sizing: border-box; }
  html, body { width: 1200px; height: 864px; overflow: hidden; }
  body {
    background: var(--backdrop);
    font-family: "Open Sans", Arial, sans-serif;
    position: relative;
  }
  .card {
    position: absolute;
    background: var(--card);
    border: 1px solid var(--card-edge);
    box-shadow: 0 14px 30px rgba(0,0,0,.45);
    color: var(--ink);
  }
  /* Front */
  .card--front { left: 70px; top: 100px; width: 520px; height: 298px; }
  .front-mark {
    position: absolute; left: 150px; top: 78px;
    display: flex; align-items: center; gap: 14px;
  }
  .front-mark__square { width: 34px; height: 34px; background: var(--mark); }
  .front-mark__name {
    font-family: "Raleway", Arial, sans-serif; font-weight: 300;
    font-size: 24px; letter-spacing: 3px; color: var(--mark);
  }
  .front-url {
    position: absolute; left: 0; right: 0; top: 196px; text-align: center;
    font-size: 13px; letter-spacing: 6px; color: var(--ink-soft);
  }
  /* Back */
  .card--back { left: 560px; top: 420px; width: 580px; height: 332px; }
  .back-mark {
    position: absolute; left: 0; right: 0; top: 46px;
    display: flex; flex-direction: column; align-items: center; gap: 10px;
  }
  .back-mark__square { width: 30px; height: 30px; background: var(--ink); }
  .back-mark__name {
    font-family: "Raleway", Arial, sans-serif; font-weight: 400;
    font-size: 24px; letter-spacing: 3px; color: var(--ink);
  }
  .holder {
    position: absolute; right: 322px; top: 172px;
    font-weight: 700; font-size: 16px; letter-spacing: .3px; text-transform: uppercase;
  }
  .divider {
    position: absolute; left: 282px; top: 158px; width: 1px; height: 126px; background: var(--ink);
  }
  .details { position: absolute; left: 300px; top: 160px; font-size: 14px; line-height: 20px; }
  .details__line { display: flex; align-items: center; gap: 8px; }
  .details__line svg { flex: none; }
  .details__indent { padding-left: 0; }
</style>
</head>
<body>
  <section class="card card--front" aria-label="Card front">
    <div class="front-mark">
      <span class="front-mark__square"></span>
      <span class="front-mark__name">FERNCLIFF ADVISORY</span>
    </div>
    <p class="front-url">www.ferncliffadvisory.com</p>
  </section>

  <section class="card card--back" aria-label="Card back">
    <div class="back-mark">
      <span class="back-mark__square"></span>
      <span class="back-mark__name">FERNCLIFF ADVISORY</span>
    </div>
    <p class="holder">Daniel Whitcombe</p>
    <span class="divider"></span>
    <div class="details">
      <p>2870 North 9th Avenue</p>
      <p>Summit Floor, Elm Ridge</p>
      <p>Illinois 60531</p>
      <p class="details__line">
        <svg width="12" height="9" viewBox="0 0 12 9"><rect x=".5" y=".5" width="11" height="8" fill="none" stroke="#f2f2f2"/><path d="M.5 .5 6 5 11.5 .5" fill="none" stroke="#f2f2f2"/></svg>
        dan@ferncliffadvisory.com
      </p>
      <p class="details__line">
        <svg width="12" height="12" viewBox="0 0 12 12"><circle cx="6" cy="6" r="5.5" fill="#f2f2f2"/><circle cx="6" cy="6" r="2" fill="#141414"/></svg>
        www.ferncliffadvisory.com
      </p>
    </div>
  </section>
</body>
</html>
```